Screen-Design für Website (Recruiting Agency)
Ich bin wirklich äußerst zufrieden mit der Arbeit und der Zusammenarbeit: tesmaruplin ist auf jeden meiner Wünsche eingegangen und hat mir auch geduldig die verschiedenesten Varianten erarbeitet, wenn ich mir mal die Vorstellungskraft fehlte. Die 5 Sterne sind mehr als verdient. __ I am really extremely satisfied with the work and the cooperation: tesmaruplin has responded to every one of my wishes and has also patiently worked out the most varied of variants for me when I lacked the imagination. The 5 stars are more than deserved.
Zielgruppe
An english version of the briefing can be found at the end
Briefing:
Kurzbeschreibung des Projektes
ich möchte ich mit einer Agentur für Recruiting zum Januar 2021 selbstständig machen und benötige für meine Website noch ein grundlegendes Screen-Design und Bilder, Kollagen und/oder Illustrationen für die verschiednen Textblöcke für zunächst vier Seiten , die die Inhalte transportieren sollen und 'Lust auf das Lesen der Texte' machen.
Ich lasse mich auch von euch Profis gerne beraten, wenn bspw. Überschriften fehlen, Call-to-Action-Elemente (bspw. Kontaktformulare) anders positioniert oder der Footer andere Inhalte enthalten sollte.
Ich benötige
Frühe Entwicklungs-/Konzeptphase als Entscheidungsgrundlage
Ein Screendesign (als PDF, JPG oder via pv.morlint.com-Webansicht) für eine der vier Seiten und die Entwicklung der dazugehörigen Bildelemente.
Am Ende des Prozesses:
- das Screendesign (als PDF, JPG oder via pv.morlint.com-Webansicht)
- Entwicklung der Bildelemente (Bilder, Kollagen oder Ilustrationen) für die verschiedenen Absätze aller vier Seiten
- webfähige Bild-Formate der einzelenen Elemente (Header, Hintergründe, Bilder) fü ride Wordpress-Umsetzung des Designs
Nachtrag 16.11.2020:
Da bereits mehrfach nachgefragt wurde, konkretisiere ich noch einmal den Ablauf (entschuldigt bitte die Verwirrung):
Ich möchte den Aufwand in der Konzeptionsphase für die teilnehmenden Designer so gering wie möglich halten, daher:
Erwarte ichzunächst ein Screendesign für eine einzige Seite . Auf dieser Basis möchte ich eine Entscheidung treffen können. Dieses Screendesign beinhaltet den grundlegenden Aufbau und das grundlegende Design der miren-Seite, die Elemente, Bilder und/oder Illustrationen, die zu dieser konkreten Seite gehören. Eventuell frage ich euch, ob ihr noch das eine oder andere an diesem Entwurf anpassen oder konkretieseren könntet.
Aufgabenstellung
An english version of the project description and goals can be found at the end
Projektbeschreibung und Ziele
Projekthintergrund
Der Vertrieb soll im Januar 2021 starten und dazu benötige ich eine professionelle Website, die die vorgenannten Zielgruppen „emotional“ zum Stöbern einlädt und neugierig auf mehr miren macht. Vertrauen schafft.
Den Dummy der Website (ein Wordpress-Theme (Varlow: https://bramuth.at/themes/varlow-overview/) mit den bereits finalen Texten finden Sie unter https://mi-kobalt.de.
Hier ist nichts „designt“, sondern dient erst einmal lediglich dazu, das Projekt und die Texte der Seiten zu transportieren und festzulegen. Also bitte nicht an den Anordnungen der Textblöcke, Farbwahl oder Schriftgrößen stören - das ist wirklich nur ein Dummy.
Konkret geht es bei diesem Auftrag um folgende vier Seiten:
_Home
_Stellenanzeigen Recruiting
_Performance Recrutiing
_Recruitment Insights
Alle weiteren Seiten (über uns, Blog, Impressum, usw.) sind exemplarisch zwar schon angelegt, werden aber zu einem späteren Zeitpunkt angegangen.
Ziele
An der Unterseite https://mi-kobalt.de/recruitment_insights/ möchte ich gerne dokumentieren, was ich genau benötige.
Die einzelnen Textblöcke der vier Unterseiten sollen durch Bilder, Collagen und/oder Illustrationen unterstützt werden, die Seite „auflockern“ und dem User helfen, schneller den jeweiligen Inhalt und seinen Vorteil zu erfassen (in der Hoffnung, dass er dann auch die dazugehörigen Texte liest).
Inspirierend fand ich bspw. Seiten wie,
https://www.quenvik.com/insights/
https://www.holdenfeld.com/recruiting-software/plexposts/,
https://www.bavorent.com/solutions/programmatic-job-advertising
https://pelzorix.com/
Wichtige Icons bzw. Logos, die mit der Branche und den Schaltkanälen in Verbindung stehen, habe ich Ihnen als PPT-Datei angehängt, falls Sie diese in einem Entwurf ve..

```html
<!DOCTYPE html>
<html lang="de">
<head>
<meta charset="utf-8">
<title>miren advisory</title>
<link rel="stylesheet" href="https://fonts.googleapis.com/css2?family=Roboto:wght@300;400;500;700;900&family=Source+Sans+3:wght@300;400;600;700&display=swap">
<style>
:root{
  --ink:#222;
  --text:#333;
  --purple-deep:#260a6e;
  --purple-mid:#4a1080;
  --purple-light:#7a1f9a;
  --band:#5a1786;
  --footer:#1c0a63;
  --white:#fff;
  --green:#1a9a2a;
  --nav-dark:#2b2b2b;
  --map:#d9dde6;
}
*{box-sizing:border-box;margin:0;padding:0}
html,body{width:1200px;height:2253px;overflow:hidden;background:var(--white)}
body{position:relative;font-family:"Source Sans 3",sans-serif;color:var(--text)}
.abs{position:absolute}

/* header */
.site-header{position:absolute;left:0;top:0;width:1200px;height:78px;background:var(--white);border-bottom:1px solid #eee}
.brand{position:absolute;left:31px;top:20px;font-family:"Source Sans 3",sans-serif;font-size:26px;font-weight:400;color:var(--ink);letter-spacing:.2px}
.nav{position:absolute;top:0;left:0;width:1200px;height:78px;font-family:"Roboto",sans-serif;font-size:15.5px;color:var(--ink)}
.nav a{position:absolute;top:29px;color:var(--ink);text-decoration:none;white-space:nowrap}
.nav .home{left:745px}
.nav .home-bar{position:absolute;left:733px;top:75px;width:66px;height:3px;background:var(--nav-dark)}
.nav .online{left:810px}
.nav .insights{left:950px;top:20px;width:161px;height:37px;line-height:37px;text-align:center;background:var(--nav-dark);color:var(--white)}
.nav .blog{left:1134px}

/* hero */
.hero{position:absolute;left:0;top:78px;width:1200px;height:731px}
.hero h1{position:absolute;left:0;top:229px;width:1265px;text-align:center;font-family:"Roboto",sans-serif;font-weight:700;font-size:51px;color:var(--white);letter-spacing:-.3px}
.hero .sub{position:absolute;left:0;top:290px;width:1265px;text-align:center;font-family:"Roboto",sans-serif;font-weight:300;font-size:51px;color:var(--white)}
.btn{position:absolute;top:396px;width:188px;height:50px;line-height:50px;text-align:center;background:var(--white);border-radius:3px;font-family:"Roboto",sans-serif;font-size:20px;box-shadow:0 4px 10px rgba(0,0,0,.2)}
.btn.start{left:411px;color:var(--green)}
.btn.more{left:657px;color:var(--purple-mid)}

/* intro */
.intro{position:absolute;left:0;top:869px;width:1200px;text-align:center;font-size:16.5px;font-weight:300;line-height:29px;color:var(--text)}
.intro h2{font-family:"Roboto",sans-serif;font-size:23px;font-weight:500;color:var(--ink);letter-spacing:.5px;margin:42px 0 23px}

/* band */
.band{position:absolute;left:0;top:1106px;width:1200px;height:318px;background:var(--band)}
.band .label{position:absolute;left:29px;top:59px;font-family:"Roboto",sans-serif;font-size:16px;color:var(--white)}
.band h3{position:absolute;left:27px;top:80px;font-family:"Roboto",sans-serif;font-weight:400;font-size:38px;color:var(--white);white-space:nowrap}
.band p{position:absolute;left:29px;top:167px;width:510px;font-family:"Roboto",sans-serif;font-size:12.2px;line-height:15px;color:var(--white)}

/* insights */
.insight{position:absolute;left:479px;top:1490px;width:680px}
.insight .label{font-size:12.5px;font-weight:400;color:#444}
.insight h3{font-family:"Roboto",sans-serif;font-size:25px;font-weight:500;color:var(--ink);letter-spacing:.5px;margin:2px 0 20px}
.insight p{font-size:17px;font-weight:300;line-height:29px;color:var(--text);margin-bottom:14px}

/* footer */
.site-footer{position:absolute;left:0;top:1768px;width:1200px;height:485px;background:var(--footer);color:var(--white)}
.site-footer h4{position:absolute;top:60px;font-family:"Roboto",sans-serif;font-weight:700;font-size:20px;letter-spacing:.4px}
.links{position:absolute;left:73px;top:102px;list-style:none;font-size:11px}
.links li{height:36.6px}
.contact{position:absolute;left:632px;top:98px;font-size:16.5px;font-weight:300;line-height:29px;width:200px}
.map{position:absolute;left:910px;top:84px;width:216px;height:200px;background:var(--map)}
.divider{position:absolute;left:0;top:428px;width:1200px;height:1px;background:rgba(255,255,255,.35)}
.copy{position:absolute;left:73px;top:452px;font-size:9px}
.to-top{position:absolute;left:1113px;top:398px;width:43px;height:43px;border:1px solid rgba(255,255,255,.4)}
.social{position:absolute;top:449px;width:9px;height:9px;border-radius:50%;background:var(--white)}
</style>
</head>
<body>

<header class="site-header">
  <div class="brand">miren advisory</div>
  <nav class="nav">
    <a class="home">Home</a>
    <span class="home-bar"></span>
    <a class="online">Online-Recruiting</a>
    <a class="insights">Recruitment Insights</a>
    <a class="blog">Blog</a>
  </nav>
</header>

<section class="hero">
  <svg class="abs" style="left:0;top:0" width="1200" height="731" viewBox="0 0 1200 731">
    <defs>
      <linearGradient id="heroGrad" x1="0.7" y1="0" x2="0.2" y2="1">
        <stop offset="0" stop-color="#28086f"/>
        <stop offset="0.55" stop-color="#4a1183"/>
        <stop offset="1" stop-color="#7a1f9a"/>
      </linearGradient>
    </defs>
    <polygon points="0,0 1200,0 1200,561 0,730" fill="url(#heroGrad)"/>
    <polygon points="0,730 0,520 650,0 1200,0 1200,200 170,706" fill="#ffffff" opacity="0.03"/>
    <g role="img" aria-label="Porträtfotos von Fachkräften mit Kanal-Kennzeichen">
      <g fill="#8a7a8c">
        <circle cx="51" cy="74" r="45"/>
        <circle cx="465" cy="79" r="45"/>
        <circle cx="1084" cy="162" r="45"/>
        <circle cx="189" cy="246" r="45"/>
        <circle cx="44" cy="424" r="45"/>
        <circle cx="306" cy="482" r="45"/>
        <circle cx="1097" cy="377" r="45"/>
        <circle cx="967" cy="499" r="45"/>
      </g>
      <g stroke="#2a0d6c" stroke-width="3">
        <circle cx="76" cy="99" r="17" fill="#5c5d66"/>
        <circle cx="490" cy="104" r="17" fill="#1877f2"/>
        <circle cx="1109" cy="187" r="17" fill="#d6307a"/>
        <circle cx="214" cy="271" r="17" fill="#5c5d66"/>
        <circle cx="67" cy="448" r="17" fill="#d6307a"/>
        <circle cx="331" cy="507" r="17" fill="#1877f2"/>
        <circle cx="1122" cy="402" r="17" fill="#5c5d66"/>
        <circle cx="992" cy="524" r="17" fill="#3a3a40"/>
      </g>
    </g>
  </svg>
  <h1>Die besten Talente gewinnen.</h1>
  <div class="sub">Stellen besetzen.</div>
  <a class="btn start">jetzt starten</a>
  <a class="btn more">mehr erfahren</a>
</section>

<section class="intro">
  <p>Online-Recruiting kann frustrierend sein: Entweder erhält man keine oder viel zu viele unpassende Bewerbungen.<br>Und doch gibt es sie: Die Talente, die perfekt zu Ihren offenen Positionen passen. Wir helfen Ihnen, die besten Talente zu erreichen.</p>
  <h2>Was wir für sie tun</h2>
  <p>Wenn Erfahrung und Leidenschaft auf Technologie treffen, dann bekommen Sie die Kandidaten, die Sie brauchen.</p>
</section>

<section class="band">
  <svg class="abs" style="left:0;top:0" width="1200" height="318" viewBox="0 0 1200 318" role="img" aria-label="Foto: zwei Geschäftsleute blicken gemeinsam auf ein Tablet">
    <defs>
      <linearGradient id="photoGrad" x1="0" y1="0" x2="1" y2="1">
        <stop offset="0" stop-color="#c9d5dc"/>
        <stop offset="0.5" stop-color="#9fb1bd"/>
        <stop offset="1" stop-color="#6e7f8e"/>
      </linearGradient>
    </defs>
    <polygon points="823,0 1200,0 1200,318 481,318" fill="url(#photoGrad)"/>
  </svg>
  <div class="label">Stellenanzeigen Recruiting</div>
  <h3>„Post &amp; Pray“ war gestern schon out</h3>
  <p>Während Ihre Wettbewerber noch „beten“, erreichen wir bereits die relevanten Kandidaten, die wirklich zu Ihren offenen Stellen passen: Zielgruppenoptimierte Stellenanzeigen auf den nachweisbar relevanten Jobbörsen, Nischen-Stellenbörsen, Netzwerken oder Special Interest-Portalen.</p>
</section>

<section class="insight">
  <div class="label">Recruiting Insights</div>
  <h3>Cleverer als Ihr Wettbewerb</h3>
  <p>Seien auch Sie cleverer als Ihre Wettbewerber: Unsere <em>Reruitment Insights</em> informieren Sie über Traffic-Trends, Arbeitsmarkt und Wettbewerb. So beurteilen Sie die Empfehlungen transparent – bvor Sie uns beauftragen. Kostenlos und unverbindlich.</p>
  <p>Damit Sie sich schneller und effizienter die besseren Talente sichern.</p>
</section>

<footer class="site-footer">
  <h4 style="left:73px">WICHTIGE LINKS</h4>
  <ul class="links">
    <li>Recruitment Insights</li>
    <li>Performance Recruiting</li>
    <li>Stellenanzeigen Recruiting</li>
    <li>Blog</li>
    <li>Datenschutz</li>
    <li>Impressum</li>
    <li>über uns</li>
    <li>Kontakt</li>
  </ul>
  <h4 style="left:632px">KONTAKT</h4>
  <div class="contact">
    miren advisory UG<br>Lindauer Str. 14b<br>65812 Oberhain am Main<br><br><br>
    Telefon +49 6190 448 217<br>E-Mail kontakt@miren-<br>advisory.de
  </div>
  <div class="map" role="img" aria-label="Kartenausschnitt mit Standort des Büros"></div>
  <div class="to-top">
    <svg width="43" height="43" viewBox="0 0 43 43"><polyline points="17,24 21.5,19.5 26,24" fill="none" stroke="#fff" stroke-width="1.5"/></svg>
  </div>
  <div class="divider"></div>
  <div class="copy">© Copyright 2020 - miren advisory UG</div>
  <span class="social" style="left:1056px"></span>
  <span class="social" style="left:1083px"></span>
  <span class="social" style="left:1109px"></span>
</footer>

</body>
</html>
```